RTavenor Business Cards & Letterhead

I have a logo but need a design for some new business cards. We are a Design-Build Firm that specializes in the design and construction of commercial projects.
the cards need to be professional. no cartoon stuff.
i would like to have the cards in AI format so I can update the card as needed. Logo is provided.
Our Address is: 4187 Marlowe Ct. Fernhaven, Westmoor 27614

```html
<!DOCTYPE html>
<html lang="en">
<head>
<meta charset="utf-8">
<title>RTavenor Business Card</title>
<link href="https://fonts.googleapis.com/css2?family=Montserrat:wght@400;500;700;800&display=swap" rel="stylesheet">
<style>
  :root {
    --backdrop: #2e2e2e;
    --card-white: #ffffff;
    --card-dark: #222222;
    --ink: #222222;
    --brand-blue: #1a74b8;
    --band: #222222;
    --paper-text: #ffffff;
  }
  * { margin: 0; padding: 0; box-sizing: border-box; }
  html, body { width: 1200px; height: 1059px; overflow: hidden; }
  body {
    background: var(--backdrop);
    font-family: "Montserrat", Arial, sans-serif;
    position: relative;
  }
  .card {
    position: absolute;
    width: 690px;
    height: 392px;
    border-radius: 24px;
    overflow: hidden;
  }
  .card-front { left: 256px; top: 100px; background: var(--card-white); }
  .card-back { left: 254px; top: 537px; background: var(--card-dark); }

  .brand {
    position: absolute;
    display: flex;
    align-items: center;
    font-weight: 800;
    letter-spacing: -0.5px;
    line-height: 1;
  }
  .brand-square { background: var(--brand-blue); flex: none; }
  .card-front .brand { left: 81px; top: 177px; font-size: 36px; color: var(--ink); gap: 8px; }
  .card-front .brand-square { width: 26px; height: 26px; }
  .card-back .brand { left: 100px; top: 166px; font-size: 70px; color: var(--paper-text); gap: 14px; }
  .card-back .brand-square { width: 52px; height: 52px; }

  .divider {
    position: absolute;
    left: 344px; top: 122px;
    width: 1.5px; height: 147px;
    background: var(--brand-blue);
  }
  .holder { position: absolute; left: 374px; top: 118px; }
  .holder-name {
    font-size: 27px; font-weight: 700; color: var(--brand-blue);
    letter-spacing: 0.8px; line-height: 1.1;
  }
  .holder-role {
    font-size: 18px; font-weight: 400; color: var(--ink);
    letter-spacing: 0.6px; line-height: 1.1;
  }
  .contact-list { position: absolute; left: 374px; top: 199px; list-style: none; }
  .contact-item {
    display: flex; align-items: center; gap: 8px;
    height: 26px; font-size: 16.5px; color: var(--ink); letter-spacing: 0.4px;
  }
  .contact-icon { width: 13px; height: 13px; flex: none; }
  .address-band {
    position: absolute; left: 0; top: 319px;
    width: 100%; height: 27px;
    background: var(--band);
    color: var(--paper-text);
    font-size: 16px; letter-spacing: 0.5px;
    display: flex; align-items: center; justify-content: center;
  }
</style>
</head>
<body>
  <section class="card card-front">
    <div class="brand"><span class="brand-square"></span>RTAVENOR</div>
    <div class="divider"></div>
    <div class="holder">
      <p class="holder-name">DANA WHITLOW</p>
      <p class="holder-role">MANAGER</p>
    </div>
    <ul class="contact-list">
      <li class="contact-item">
        <svg class="contact-icon" viewBox="0 0 16 16"><path fill="#1a74b8" d="M3.5 1.5l2.3 2.6-1.3 1.6c.9 2 2.6 3.9 4.8 4.9l1.6-1.3 2.6 2.3-1.5 2.4C6.8 13.5 2.4 9.2 1.3 3z"/><path d="M9 3a4 4 0 0 1 4 4M9 .8A6.2 6.2 0 0 1 15.2 7" fill="none" stroke="#1a74b8" stroke-width="1.3"/></svg>
        123-456-7890
      </li>
      <li class="contact-item">
        <svg class="contact-icon" viewBox="0 0 16 16"><rect x="1" y="3" width="14" height="10" rx="1" fill="#1a74b8"/><path d="M1.5 4l6.5 5 6.5-5" fill="none" stroke="#fff" stroke-width="1.3"/></svg>
        info@youremail.com
      </li>
      <li class="contact-item">
        <svg class="contact-icon" viewBox="0 0 16 16" fill="none" stroke="#1a74b8" stroke-width="1.2"><circle cx="8" cy="8" r="6.5"/><ellipse cx="8" cy="8" rx="3" ry="6.5"/><path d="M1.5 8h13M2.5 4.8h11M2.5 11.2h11"/></svg>
        www.yourwebsite.com
      </li>
    </ul>
    <div class="address-band">4187 Marlowe Ct. Fernhaven, Westmoor 27614</div>
  </section>

  <section class="card card-back">
    <div class="brand"><span class="brand-square"></span>RTAVENOR</div>
  </section>
</body>
</html>
```